Unlock Your Way Upward Promotional Flyer

I Need a one page, one-sided 8.5 x 11 editable promotional flyer that POPS!, designed in photoshop

[TITLE]Unlock Your Way Upward: 3 BOLD Moves to Up-Level Your Business Now!

[CONTENT for the Flyer:]

At this content-rich event you will learn how to:
• Get out of feast and famine mode and into six, multi-six and/or seven figure-income mode
• Leapfrog your competition and become the obvious choice in your market
• Have your business aligned with who you are and what you want
• Enjoy your business far more than you imagined possible.
• Have more fun and time to yourself
• Live free and unbound!

Accolades
“Delphine helped us increase our six figure income by 41%...I feel reborn!” Marlene & Curtis Pettibone, Vienna, VA

“…Delphine is a joy to listen to - compelling, smart, provocative…” – Dennis Whitcombe, Charlotte, North Carolina

“Delphine helped me increase my business by 66%...without me spending more time, money, or making cold calls! …I am in the zone!” Kay Standish, Baltimore, MD
“Delphine is an energetic and dynamic speaker…content-rich…holds your attention to the very end!” Walt Pruitt, Frmr Pres., Hale & Brandt, MD, MD, D.C., PA, DE, NJ
“Delphine is the real estate whisperer!” Tom Garvey, Washington D.C.

“Delphine was prepared, funny, informative and made a connection with each of our agents…Fabulous!…even my admins were PUMPED!!! – Paul Denholm, New York

About Delphine:
Delphine is a highly regarded business development speaker & coach who knows how to pump up an audience and have them making more money, in less time, AND having more fun doing it! What’s not to love?! Consistently rated as an exceptional speaker and conference favorite! Among her work: Standing Apart: How to Draw Your Perfect Buyers Time After Time!, Finding Buyers Without Fuss, The Worst Outreach Errors Real Estate Agents Commit and How to Sidestep Them, Hard Seasons Build Hardy Brokers, Drive Within for Real Estate Agents.

[Also need a section for:]
Date: December 9, 2015, Time: 9:00 Am - 12:00 Noon, Place: Copper Lantern Convention, Ashford Mill, PA

Target Market(s)

Real Estate Agents

Industry/Entity Type

Real Estate Agent

Font styles to use
Sans Serif

Colors
0655a3
f37122

Requirements
Must have
• the top tier property mentor logo
Nice to have
• unlock your way upward logo; lots of POP! :-) ; open to other colors, accent colors.

```html
<!DOCTYPE html>
<html lang="en">
<head>
<meta charset="utf-8">
<title>Unlock Your Way Upward – Event Flyer</title>
<link href="https://fonts.googleapis.com/css2?family=Roboto:wght@400;500;700&display=swap" rel="stylesheet">
<style>
  :root {
    --navy: #0b2f6b;
    --blue: #0655a3;
    --orange: #f37122;
    --panel: #e8e8e8;
    --text: #555555;
    --rule: #d6d6d6;
    --white: #ffffff;
  }
  * { margin: 0; padding: 0; box-sizing: border-box; }
  html, body { width: 927px; height: 1200px; overflow: hidden; background: var(--white); }
  body { font-family: "Roboto", Arial, sans-serif; color: var(--text); }
  .flyer { position: relative; width: 927px; height: 1200px; overflow: hidden; background: var(--white); }

  .header-wave { position: absolute; top: 0; left: 0; width: 927px; height: 130px; }
  .brand-mark {
    position: absolute; top: 34px; right: 52px;
    font-size: 30px; font-weight: 500; color: var(--white); letter-spacing: -0.5px;
  }

  .speaker-photo {
    position: absolute; left: 215px; top: 92px; width: 215px; height: 193px;
    background: linear-gradient(160deg, #e9d6c2 0%, #c9a584 45%, #2b2b2b 100%);
  }
  .coach-logo {
    position: absolute; left: 14px; top: 135px; width: 200px;
    font-size: 24px; font-weight: 700; line-height: 1.1; color: #6b6b6b;
  }
  .coach-tagline {
    position: absolute; left: 0; top: 285px; width: 427px; height: 28px;
    background: #c85a12; color: var(--white);
    font-size: 14px; font-style: italic; text-align: center; line-height: 28px;
  }

  .about {
    position: absolute; left: 0; top: 313px; width: 427px; height: 366px;
    background: var(--blue); color: var(--white); padding: 10px 16px 0 18px;
  }
  .about h2 { font-size: 21px; font-weight: 700; margin-bottom: 4px; }
  .about p { font-size: 16.6px; line-height: 28px; text-align: justify; hyphens: auto; }

  .event-panel {
    position: absolute; left: 432px; top: 121px; width: 495px; height: 558px;
    background: var(--panel); padding: 42px 20px 0 20px;
  }
  .event-title { font-size: 35px; font-weight: 700; color: var(--orange); line-height: 1.1; }
  .event-subtitle { font-size: 27px; font-weight: 700; color: var(--blue); line-height: 40px; margin-top: 4px; }
  .learn-heading { font-size: 19px; font-weight: 700; color: var(--blue); margin-top: 4px; }
  .benefits { list-style: none; margin-top: 14px; }
  .benefits li {
    position: relative; padding-left: 38px; font-size: 17.3px; line-height: 23px;
    margin-bottom: 14px; text-align: justify;
  }
  .benefits li.single { margin-bottom: 20px; }
  .benefits svg { position: absolute; left: 3px; top: 5px; width: 22px; height: 18px; }

  .testimonials { position: absolute; left: 0; top: 692px; width: 927px; }
  .testimonials h2 { font-size: 23px; font-weight: 700; color: var(--orange); padding-left: 18px; margin-bottom: 6px; }
  .quote {
    font-size: 17px; line-height: 24px; padding: 7px 18px 9px 20px;
    border-bottom: 1px solid var(--rule); margin-right: 18px;
  }
  .quote:last-child { border-bottom: none; }
  .quote .who { color: var(--blue); }

  .footer-wave { position: absolute; left: 0; top: 1075px; width: 927px; height: 125px; }
  .event-details { position: absolute; left: 248px; top: 1133px; color: var(--white); font-size: 17px; font-weight: 700; line-height: 28px; }
  .details-divider { position: absolute; left: 485px; top: 1134px; width: 1px; height: 54px; background: rgba(255,255,255,0.6); }
  .event-place { position: absolute; left: 501px; top: 1161px; color: var(--white); font-size: 17.5px; font-weight: 700; }
</style>
</head>
<body>
<div class="flyer">

  <svg class="header-wave" viewBox="0 0 927 130" aria-hidden="true">
    <path d="M150,0 H927 V118 Q640,120 470,60 Q380,22 150,0 Z" fill="var(--orange)"/>
    <path d="M150,0 H927 V108 Q650,112 480,55 Q390,20 150,0 Z" fill="var(--navy)"/>
  </svg>
  <div class="brand-mark">Unlock Your Way Upward</div>

  <div class="coach-logo">Delphine Marsh The Top Tier Property Mentor</div>
  <div class="speaker-photo" role="img" aria-label="Portrait photo of Delphine Marsh"></div>
  <div class="coach-tagline">“America’s Top Tier Property Mentor”™</div>

  <section class="about">
    <h2>About Delphine</h2>
    <p>Delphine is a highly regarded business development speaker &amp; coach who knows how to pump up an audience and have them making more money, in less time, AND having more fun doing it! What’s not to love?! Consistently rated as an exceptional speaker and conference favorite! Among her work: Standing Apart: How to Draw Your Perfect Buyers Time After Time!, Finding Buyers Without Fuss, The Worst Outreach Errors Real Estate Agents Commit and How to Sidestep Them, Hard Seasons Build Hardy Brokers, Drive Within for Real Estate Agents.</p>
  </section>

  <section class="event-panel">
    <h1 class="event-title">Unlock Your Way Upward:</h1>
    <p class="event-subtitle">3 BOLD Moves to Up-Level Your Business Now!</p>
    <p class="learn-heading">At this content-rich event you will learn how to:</p>
    <ul class="benefits">
      <li><svg viewBox="0 0 22 18"><path d="M1,10 L8,16 L21,2 L8,11 Z" fill="#666"/></svg>Get out of feast and famine mode and into six, multi-six and/or seven figure-income mode</li>
      <li><svg viewBox="0 0 22 18"><path d="M1,10 L8,16 L21,2 L8,11 Z" fill="#666"/></svg>Leapfrog your competition and become the obvious choice in your market</li>
      <li><svg viewBox="0 0 22 18"><path d="M1,10 L8,16 L21,2 L8,11 Z" fill="#666"/></svg>Have your business aligned with who you are and what you want</li>
      <li><svg viewBox="0 0 22 18"><path d="M1,10 L8,16 L21,2 L8,11 Z" fill="#666"/></svg>Enjoy your business far more than you imagined possible.</li>
      <li class="single"><svg viewBox="0 0 22 18"><path d="M1,10 L8,16 L21,2 L8,11 Z" fill="#666"/></svg>Have more fun and time to yourself</li>
      <li><svg viewBox="0 0 22 18"><path d="M1,10 L8,16 L21,2 L8,11 Z" fill="#666"/></svg>Live free and unbound!</li>
    </ul>
  </section>

  <section class="testimonials">
    <h2>Our Happy Testimonials</h2>
    <p class="quote">“Delphine helped us increase our six figure income by 41%...I feel reborn!” <span class="who">- Marlene &amp; Curtis Pettibone, Vienna, VA</span></p>
    <p class="quote">“…Delphine is a joy to listen to - compelling, smart, provocative…” <span class="who">– Dennis Whitcombe, Charlotte, North Carolina</span></p>
    <p class="quote">“Delphine helped me increase my business by 66%...without me spending more time, money, or making cold calls! …I am in the zone!” <span class="who">- Kay Standish, Baltimore, MD</span></p>
    <p class="quote">“Delphine is an energetic and dynamic speaker… content-rich… holds your attention to the very end!”<br><span class="who">- Walt Pruitt, Frmr Pres., Hale &amp; Brandt, MD, MD, D.C., PA, DE, NJ</span></p>
    <p class="quote">“Delphine is the real estate whisperer!” <span class="who">- Tom Garvey, Washington D.C.</span></p>
    <p class="quote">“Delphine was prepared, funny, informative and made a connection with each of our agents…Fabulous!…even my admins were PUMPED!!! <span class="who">– Paul Denholm, New York</span></p>
  </section>

  <svg class="footer-wave" viewBox="0 0 927 125" aria-hidden="true">
    <path d="M0,45 Q420,0 927,22 V125 H0 Z" fill="var(--navy)"/>
    <path d="M0,52 Q430,14 927,34 V125 H0 Z" fill="var(--white)"/>
    <path d="M0,62 Q430,24 927,42 V125 H0 Z" fill="var(--orange)"/>
  </svg>
  <div class="event-details">Date: December 9, 2015<br>Time: 9:00 Am - 12:00 Noon</div>
  <div class="details-divider"></div>
  <div class="event-place">Place: Copper Lantern Convention, Ashford Mill, PA</div>

</div>
</body>
</html>
```